The World Most Wanted Eyelahes

1. We need a web design for a new company based in California, USA
2. We are the manufacturer for 100% human hair eyelashes,
made in Indonesia.
3. We recently launched "Tapered Eyelashes" with human hair.
Currently, none of the people carried Tapered eyelash.
4. We would like to see designs that use the 4 different colors that match with my products as "Four Seasons" concepts.
5. We prefer to follow www.pelvo.com style, like professional website.
6. Focus on products as a manufacturer, therefore, all wholesaler and retailer copy and paste to their marketing tools.
7. Need bilingual English and Spanish.
8. Easy to link with social media.

Target Market(s)

United States and Central/South America.

Industry/Entity Type

Hair

Number of Pages Required

5+ page

Requirements
Must have
• 1. Details of Products with image.
• 2. Hottest/Newest Items "Tapered in 100% Human Hair"
• 3. Store Page
Nice to have
• 1. My competitors is Quorim Eyelash. http://www.quorimlashes.com/
• Please follow the concepts of it.
• 2. www.Pelvo.com: They have great products detail on the website.
• i would like to focus on "Tapered" for new styles of the eyelash.
• 3. I want to visitors can write down the "Reviews" in every single product.
• Please check the www.QTRCosmetics.com.
Should not have
• It's not salon/Shop for the beauty.
• No need an appointment.
• We are the manufacturer of the eyelash.

```html
<!DOCTYPE html>
<html lang="en">
<head>
<meta charset="utf-8">
<title>Lumeva — Tapered in 100% Human Hair</title>
<link rel="stylesheet" href="https://fonts.googleapis.com/css2?family=Raleway:wght@400;500;600&family=Open+Sans:wght@400;600&display=swap">
<style>
  :root {
    --page-bg: #f1f1f1;
    --column-bg: #ffffff;
    --gold: #d9a514;
    --gold-dark: #c98a0c;
    --gold-deep: #c07c0a;
    --gold-text: #b8862a;
    --ink: #3a3a3a;
    --body-text: #666666;
    --white: #ffffff;
    --border: #d8d8d8;
    --pink: #f34f7c;
    --pink-dark: #e93f6d;
    --blue: #7cc3f2;
    --blue-dark: #5aaee9;
    --yellow: #f5c327;
    --yellow-dark: #eeb214;
    --purple: #a3309a;
    --purple-dark: #8f2486;
  }
  * { box-sizing: border-box; margin: 0; padding: 0; }
  html, body { width: 1200px; height: 1180px; overflow: hidden; }
  body { background: var(--page-bg); font-family: "Open Sans", Arial, sans-serif; color: var(--ink); }

  .site { position: absolute; left: 192px; top: 0; width: 815px; height: 1180px; background: var(--column-bg); }

  /* Header */
  .site-header { position: relative; height: 97px; }
  .brand { position: absolute; left: 26px; top: 28px; display: flex; align-items: center; gap: 10px; }
  .brand-mark { width: 12px; height: 12px; border-radius: 50%; background: var(--gold-text); }
  .brand-name { font-family: "Raleway", sans-serif; font-weight: 400; font-size: 40px; letter-spacing: 1px; color: var(--gold-text); line-height: 1; }
  .lang-select { position: absolute; left: 712px; top: 23px; width: 78px; height: 23px; border: 1px solid #cfcfcf; display: flex; align-items: center; padding-left: 7px; gap: 6px; font-size: 10px; color: #333; }
  .lang-flag { width: 16px; height: 11px; }
  .lang-caret { width: 7px; height: 5px; margin-left: 2px; }
  .search { position: absolute; left: 591px; top: 56px; width: 195px; height: 24px; border: 1px solid #c9c9c9; box-shadow: inset 0 1px 2px rgba(0,0,0,.08); display: flex; align-items: center; padding: 0 8px 0 10px; justify-content: space-between; }
  .search-placeholder { font-size: 9px; font-style: italic; color: #777; }
  .search-icon { width: 14px; height: 14px; }

  /* Navigation */
  .main-nav { display: flex; height: 40px; background: linear-gradient(to bottom, var(--gold) 0%, var(--gold-dark) 100%); }
  .main-nav a { display: flex; align-items: center; justify-content: center; font-family: "Raleway", sans-serif; font-weight: 500; font-size: 14px; color: var(--white); text-decoration: none; border-right: 1px solid rgba(150,95,0,.45); box-shadow: 1px 0 0 rgba(255,230,150,.35); }
  .main-nav a:last-child { border-right: none; box-shadow: none; }

  /* Hero */
  .hero { position: relative; height: 366px; }
  .hero-photo { position: absolute; inset: 0; background:
      radial-gradient(ellipse 40% 60% at 75% 45%, #d49a6a 0%, rgba(180,110,60,0) 70%),
      radial-gradient(ellipse 25% 45% at 92% 45%, #e4b43c 0%, rgba(200,150,40,0) 75%),
      linear-gradient(to right, #5a2e10 0%, #8a5224 35%, #a66a34 60%, #7a4a1e 100%); }
  .hero-copy { position: absolute; left: 59px; top: 112px; color: var(--white); font-family: "Raleway", sans-serif; }
  .hero-kicker { font-size: 33px; font-weight: 500; line-height: 1.1; letter-spacing: .3px; }
  .hero-title { font-size: 50px; font-weight: 500; line-height: 1.1; letter-spacing: .3px; }
  .hero-dots { position: absolute; left: 62px; top: 204px; display: flex; gap: 7px; }
  .hero-dots span { width: 13px; height: 13px; border-radius: 50%; background: rgba(255,255,255,.45); }
  .hero-dots span.is-active { background: var(--white); }

  /* Intro */
  .intro { text-align: center; padding-top: 41px; }
  .intro-title { font-family: "Raleway", sans-serif; font-weight: 500; font-size: 25px; color: #333; line-height: 1.2; }
  .intro-subtitle { font-family: "Raleway", sans-serif; font-weight: 500; font-size: 18px; color: #333; line-height: 1.35; }
  .intro-text { width: 745px; margin: 11px auto 0; font-size: 10.6px; line-height: 15.4px; color: var(--body-text); }

  /* Product seasons */
  .product-row { position: absolute; left: 15px; top: 700px; display: flex; gap: 6px; }
  .product-card { width: 192px; height: 193px; border: 1px solid var(--border); display: flex; flex-direction: column; overflow: hidden; }
  .product-image { flex: 1; display: flex; align-items: center; justify-content: center; }
  .product-pack { width: 104px; height: 120px; border-radius: 16px 16px 10px 10px; }
  .product-label { height: 52px; padding: 9px 0 0 17px; color: var(--white); white-space: nowrap; }
  .product-name { font-family: "Raleway", sans-serif; font-weight: 500; font-size: 14px; letter-spacing: -0.1px; line-height: 1.2; }
  .product-tagline { font-family: "Raleway", sans-serif; font-size: 9.5px; margin-top: 3px; opacity: .9; }
  .season-blossom .product-label { background: linear-gradient(var(--pink), var(--pink-dark)); }
  .season-blossom .product-pack { background: linear-gradient(160deg, #f6c3cf, #5a2f3a); }
  .season-dazzling .product-label { background: linear-gradient(var(--blue), var(--blue-dark)); }
  .season-dazzling .product-pack { background: linear-gradient(160deg, #d9e6ef, #8fa6b6); }
  .season-sparkling .product-label { background: linear-gradient(var(--yellow), var(--yellow-dark)); }
  .season-sparkling .product-pack { background: linear-gradient(160deg, #c58a3c, #3b2414); }
  .season-fascinating .product-label { background: linear-gradient(var(--purple), var(--purple-dark)); }
  .season-fascinating .product-pack { background: linear-gradient(160deg, #c43d9a, #3c1a4c); }

  /* Footer */
  .site-footer { position: absolute; left: 0; top: 959px; width: 815px; height: 221px; }
  .footer-links { position: relative; height: 180px; background: linear-gradient(to bottom, var(--gold) 0%, var(--gold-deep) 100%); }
  .footer-col { position: absolute; top: 31px; color: var(--white); }
  .footer-col h3 { font-family: "Raleway", sans-serif; font-weight: 500; font-size: 17px; line-height: 1; margin-bottom: 7px; }
  .footer-col a { display: block; font-size: 11.5px; line-height: 21px; color: var(--white); text-decoration: none; }
  .footer-bottom { height: 41px; background: var(--gold); padding: 15px 0 0 46px; font-size: 9.5px; color: var(--white); }
</style>
</head>
<body>
  <div class="site">
    <header class="site-header">
      <div class="brand">
        <span class="brand-name">LUMEVA</span>
        <span class="brand-mark"></span>
      </div>
      <div class="lang-select">
        <svg class="lang-flag" viewBox="0 0 16 11" aria-hidden="true"><rect width="16" height="11" fill="#2b3f8c"/><rect y="4" width="16" height="3" fill="#fff"/><rect x="6.5" width="3" height="11" fill="#fff"/><rect y="4.7" width="16" height="1.6" fill="#d22"/><rect x="7.2" width="1.6" height="11" fill="#d22"/></svg>
        <span>English</span>
        <svg class="lang-caret" viewBox="0 0 7 5" aria-hidden="true"><path d="M0 0h7L3.5 5z" fill="#444"/></svg>
      </div>
      <div class="search">
        <span class="search-placeholder">Search here</span>
        <svg class="search-icon" viewBox="0 0 14 14" aria-hidden="true"><circle cx="6" cy="6" r="4.5" fill="none" stroke="#888" stroke-width="1.8"/><path d="M9.3 9.3L13 13" stroke="#888" stroke-width="2" stroke-linecap="round"/></svg>
      </div>
    </header>

    <nav class="main-nav">
      <a href="#" style="width:93px">HOME</a>
      <a href="#" style="width:120px">ABOUT US</a>
      <a href="#" style="width:122px">PRODUCTS</a>
      <a href="#" style="width:113px">SPECIALS</a>
      <a href="#" style="width:119px">BUY NOW</a>
      <a href="#" style="width:114px">SUPPORT</a>
      <a href="#" style="width:134px">CONTACT</a>
    </nav>

    <section class="hero">
      <div class="hero-photo" role="img" aria-label="Beauty portrait of a model with gold makeup and golden flowers on a warm bokeh background"></div>
      <div class="hero-copy">
        <p class="hero-kicker">TAPERED IN 100%</p>
        <h1 class="hero-title">HUMAN HAIR</h1>
      </div>
      <div class="hero-dots"><span class="is-active"></span><span></span><span></span><span></span></div>
    </section>

    <section class="intro">
      <h2 class="intro-title">Lorem ipsum dolor sit amet consectetuer adipiscing elit</h2>
      <p class="intro-subtitle">Mauris vel lacus vitae felis vestibulum volutpat Etiam</p>
      <p class="intro-text">Morbi ornare gravida elit Integer congue augue et malesuada iaculis ipsum dui aliquet felis at cursus magna nisl nec elit Praesent elementum elit at tellus<br>nec ultricies sit amet porttitor mattis enim In massa libero interdum nec interdum vel blandit sed nulla In ullamcorper est eget tempor cursus neque mi<br>consectetuer mi a ultricies massa est sed nisl Class aptent taciti sociosqu ad litora torquent per conubia</p>
    </section>

    <section class="product-row">
      <article class="product-card season-blossom">
        <div class="product-image"><div class="product-pack" role="img" aria-label="Pink eyelash product package"></div></div>
        <div class="product-label"><h3 class="product-name">BLOSSOM YOUR EYE</h3><p class="product-tagline">MAURIS VEL LACUS VITAE FELIS</p></div>
      </article>
      <article class="product-card season-dazzling">
        <div class="product-image"><div class="product-pack" role="img" aria-label="Blue eyelash product package"></div></div>
        <div class="product-label"><h3 class="product-name">DAZZLING YOUR EYE</h3><p class="product-tagline">MAURIS VEL LACUS VITAE FELIS</p></div>
      </article>
      <article class="product-card season-sparkling">
        <div class="product-image"><div class="product-pack" role="img" aria-label="Gold eyelash product package"></div></div>
        <div class="product-label"><h3 class="product-name">SPARKLING YOUR EYE</h3><p class="product-tagline">MAURIS VEL LACUS VITAE FELIS</p></div>
      </article>
      <article class="product-card season-fascinating">
        <div class="product-image"><div class="product-pack" role="img" aria-label="Purple eyelash product package"></div></div>
        <div class="product-label"><h3 class="product-name">FASCINATING YOUR EYE</h3><p class="product-tagline">MAURIS VEL LACUS VITAE FELIS</p></div>
      </article>
    </section>

    <footer class="site-footer">
      <div class="footer-links">
        <div class="footer-col" style="left:43px"><h3>Company</h3><a href="#">About Us</a><a href="#">Our Products</a><a href="#">Best Sellings</a><a href="#">Product Flavours</a></div>
        <div class="footer-col" style="left:196px"><h3>Best Products</h3><a href="#">Class aptent</a><a href="#">Taciti sociosqu ad</a><a href="#">Litora torquent</a><a href="#">Conubia nostra</a></div>
        <div class="footer-col" style="left:384px"><h3>Resources</h3><a href="#">Support</a><a href="#">Order Now</a><a href="#">Testmonials</a><a href="#">Privacy Policy</a></div>
        <div class="footer-col" style="left:530px"><h3>Support</h3><a href="#">Support</a><a href="#">Contact Us</a><a href="#">Term of Use</a><a href="#">Privacy Policy</a></div>
        <div class="footer-col" style="left:668px"><h3>Get in touch</h3><a href="#">Support</a><a href="#">Contact Us</a><a href="#">Term of Use</a><a href="#">Privacy Policy</a></div>
      </div>
      <div class="footer-bottom">© 2015 Company Name &nbsp;All right reserved &nbsp;Term of Use</div>
    </footer>
  </div>
</body>
</html>
```